Wordpress Web Design & Coding for velcorahealth.ca

We need a website for a new investment company that is visually grabbing and vibrant. We would like to see a web page that displays trust, growth and confidence. Needs to be responsive and mobile friendly for all browsers and coded for both Android & IOS.

Open to the number of pages and menu items. I selected 4 but if you feel the layout would work better with less I am open to this. Need to sell the people (management team/related businesses) and then show where the invested money will be going (upcoming projects).

Company Info:

Vel Cora is an investment company put together by a group of seasoned business professionals who have come together to combine decades of success in the real estate development, management, financing and medical services. The company will be a full service company offering turn key solutions for medical professionals.

Vel-Cora will focus on providing a full range of services via a group of distinct companies to deliver newly emerging needs of the medical community. The end goal will be to create complete solutions for individuals in the medical community. Our group has experience and success with the conceptualization, construction and financing of medical and dental clinic spaces. Vel-Cora Solutions will be established to accommodate all areas of the development and creation of clinics for medical professionals from building construction to equipment financing and administrations.

You can mention these companies and take photos from their websites. You can also use stock photos.

Our construction partner:
https://318bld.com/projects/

Our equipment leasing partner:
https://www.norvixa.com/

Our Management Team and medical partners

Gil Parish
https://www.ourfirmstance.ca/

Dietmar Vellasquin
https://www.gshdentalservices.com/about-us

PROPOSED PROJECTS (see attachment for details)
Pinegrove Business Park
Holtmere Business Park
Mt. Corwin Ridge Professional

Target Market(s)

Investors

Industry/Entity Type

Investment

Coding

Coded - Design and coding required

Number of Pages Required

4 page

Font styles to use
Sans Serif

Requirements
Must have
• Wordpress – must be both desktop and mobile friendly with fast page load speed
Ability to edit after ourselves in Wordpress
Attractive home page with logo etc.
Logo colours are: for the blue the pantone color is #0355a3
and for the green is #8cc63f

Sections, about us, what we do/services we provide, contact us

```html
<!DOCTYPE html>
<html lang="en">
<head>
<meta charset="utf-8">
<title>Vel-Cora Solutions</title>
<link rel="stylesheet" href="https://fonts.googleapis.com/css2?family=Montserrat:wght@400;500;600;700&family=Roboto+Condensed:wght@700&family=Arimo:wght@400;700&display=swap">
<style>
:root{
  --blue:#0355a3;
  --blue-band:#3a78c4;
  --green:#8cc63f;
  --ink:#1a1a1a;
  --text:#333;
  --muted:#777;
  --light:#f5f6f8;
  --white:#fff;
}
*{box-sizing:border-box;margin:0;padding:0}
html,body{width:1200px;height:3306px;overflow:hidden;background:var(--white)}
body{position:relative;font-family:"Arimo",Arial,sans-serif;color:var(--text)}
.abs{position:absolute}
.btn{position:absolute;display:flex;align-items:center;justify-content:center;background:var(--green);color:var(--white);font-family:"Montserrat",sans-serif;font-weight:500;font-size:15px;border-radius:4px;letter-spacing:.3px}
.sec-title{position:absolute;left:0;width:1200px;text-align:center;font-family:"Montserrat",sans-serif;font-weight:700;font-size:41px;letter-spacing:.5px;color:var(--blue)}
.sec-title .accent{color:var(--green)}

/* header */
.topbar{left:597px;top:0;width:603px;height:38px;background:var(--green);clip-path:polygon(0 0,100% 0,100% 100%,40px 100%)}
.topbar-item{top:11px;color:var(--white);font-family:"Montserrat",sans-serif;font-size:14px;font-weight:500;display:flex;align-items:center;gap:7px}
.brand{left:141px;top:20px;font-family:"Montserrat",sans-serif;font-weight:700;color:var(--blue);font-size:25px;line-height:1;display:flex;align-items:center;gap:9px}
.brand-mark{width:14px;height:14px;background:var(--blue)}
.nav{top:68px;font-family:"Montserrat",sans-serif;font-size:15px;color:#333;letter-spacing:.3px}
.nav.active{color:var(--blue);font-weight:600}

/* hero */
.hero{left:0;top:99px;width:1200px;height:594px;background:linear-gradient(180deg,#a8d9df 0%,#7cc3cd 45%,#93cdd6 100%)}
.hero-birds{left:540px;top:230px;width:600px;height:340px;background:radial-gradient(ellipse at center,rgba(40,70,80,.22),rgba(40,70,80,0) 70%)}
.hero-title{left:142px;top:296px;width:520px;font-family:"Roboto Condensed",sans-serif;font-weight:700;font-size:24px;line-height:35px;color:#0f2a3a;white-space:nowrap}
.hero-title .accent{color:var(--blue)}

/* about */
.about-kicker{left:0;top:784px;width:1200px;text-align:center;font-family:"Montserrat",sans-serif;font-size:24px;color:var(--blue);font-weight:500}
.about-lead{left:150px;top:880px;width:900px;text-align:center;font-weight:700;font-size:17px;line-height:31px;color:var(--ink)}
.about-body{left:160px;top:950px;width:880px;text-align:center;font-size:14.2px;line-height:25.5px;color:#333}
.about-body p+p{margin-top:11px}

/* solutions */
.band{left:0;top:1668px;width:1200px;height:296px;background:var(--blue-band)}
.sol-img{top:1401px;width:428px;height:247px}
.sol-card{top:1668px;width:438px;height:135px;background:var(--white);border-radius:4px;text-align:center;padding-top:10px}
.sol-card h3{font-family:"Montserrat",sans-serif;font-weight:500;font-size:19px;color:var(--ink);letter-spacing:.3px}
.sol-card p{font-size:12.5px;line-height:23px;margin:8px auto 0;width:380px;color:#222}

/* projects */
.proj-img{top:2114px;width:291px;height:338px;border-radius:4px}
.proj-card{top:2383px;width:248px;height:110px;background:var(--white);border-bottom:2px solid var(--green);box-shadow:0 3px 10px rgba(0,0,0,.12);padding:18px 12px 0}
.proj-card h4{font-family:"Arimo",sans-serif;font-weight:700;font-size:17.5px;color:var(--ink);white-space:nowrap}
.proj-card h4.long{font-size:15.5px}
.proj-card p{font-size:11.5px;line-height:21px;margin-top:6px;color:#222}
.arrow{top:2265px;width:34px;height:34px;border-radius:50%;display:flex;align-items:center;justify-content:center}

/* team */
.team-bg{left:0;top:2576px;width:1200px;height:474px;background:var(--light)}
.tab{top:2647px;height:38px;border-radius:3px;display:flex;align-items:center;justify-content:center;font-family:"Montserrat",sans-serif;font-weight:500;font-size:14.5px;letter-spacing:.3px}
.tab-outline{border:2px solid var(--blue);color:var(--blue);background:var(--white)}
.tab-filled{background:var(--green);color:var(--white)}
.member{top:2729px;width:438px;height:250px;background:var(--white);box-shadow:0 2px 8px rgba(0,0,0,.08)}
.member-photo{left:5px;top:4px;width:217px;height:243px}
.member-info{left:239px;top:33px;width:190px}
.member-info h5{font-family:"Montserrat",sans-serif;font-weight:600;font-size:17px;color:var(--blue);white-space:nowrap}
.member-brand{margin-top:12px;font-family:"Arimo",sans-serif;font-weight:400;font-size:22px;color:var(--muted);line-height:1}
.member-info p{font-size:11px;line-height:20.5px;color:#222;margin-top:14px}

/* footer */
.footer{left:0;top:3050px;width:1200px;height:256px;background:var(--blue)}
.fnav{top:3096px;font-family:"Montserrat",sans-serif;font-size:13.5px;color:var(--white);letter-spacing:.3px}
.fsep{top:3094px;width:1px;height:18px;background:rgba(255,255,255,.35)}
.fline{left:141px;top:3140px;width:918px;height:1px;background:rgba(255,255,255,.25)}
.fcontact{top:3172px;display:flex;gap:13px;color:var(--white)}
.ficon{width:34px;height:34px;border-radius:50%;background:var(--green);display:flex;align-items:center;justify-content:center;flex:none}
.fcontact h6{font-family:"Montserrat",sans-serif;font-size:13.5px;font-weight:600}
.fcontact p{font-family:"Montserrat",sans-serif;font-size:11.5px;line-height:17px;margin-top:2px}
.fdiv{top:3168px;height:56px;border-left:1px dashed rgba(255,255,255,.4)}
.copy{left:142px;top:3271px;font-family:"Montserrat",sans-serif;font-size:11.5px;color:var(--white)}
.social{top:3266px;width:23px;height:23px;border:1.5px solid var(--white);border-radius:50%}
</style>
</head>
<body>

<!-- header -->
<div class="abs topbar"></div>
<div class="abs topbar-item" style="left:657px">
  <svg width="14" height="14" viewBox="0 0 24 24" fill="none" stroke="#0355a3" stroke-width="2.2"><path d="M5 3h4l2 5-3 2a12 12 0 0 0 6 6l2-3 5 2v4a2 2 0 0 1-2 2A17 17 0 0 1 3 5a2 2 0 0 1 2-2z"/></svg>
  +1 123 456 7890
</div>
<div class="abs topbar-item" style="left:830px">
  <svg width="16" height="12" viewBox="0 0 24 18" fill="none" stroke="#0355a3" stroke-width="2"><rect x="1" y="1" width="22" height="16" rx="2"/><path d="M1 2l11 8 11-8"/></svg>
  info@velcorahealth.com
</div>
<div class="abs brand"><span class="brand-mark"></span>VEL-CORA<br>SOLUTIONS</div>
<div class="abs nav active" style="left:584px">HOME</div>
<div class="abs nav" style="left:681px">ABOUT US</div>
<div class="abs nav" style="left:808px">WHAT WE DO</div>
<div class="abs nav" style="left:962px">CONTACT US</div>

<!-- hero -->
<div class="abs hero" role="img" aria-label="Sky above soft clouds with a flock of birds flying in formation"></div>
<div class="abs hero-birds" role="img" aria-label="Flock of birds"></div>
<div class="abs hero-title"><span class="accent">VEL-CORA</span> Is An Investment Company<br>With Focus on Providing A Full Range<br>of Services, For The Newly Emerging<br>Needs of The Medical Community</div>
<div class="btn" style="left:142px;top:452px;width:171px;height:37px">CALL US TODAY &#8594;</div>

<!-- about -->
<div class="abs about-kicker">ABOUT</div>
<div class="sec-title" style="top:818px">VEL-CORA <span class="accent">SOLUTIONS</span></div>
<div class="abs about-lead">Vel-Cora will focus on providing a full range of services via a group of distinct companies to deliver<br>newly emerging needs of the medical community.</div>
<div class="abs about-body">
  <p>The end goal will be to create complete solutions for individuals in the medical community. Our group has experience and success<br>with the conceptualization, construction and financing of medical and dental clinic spaces. Vel-Cora Solutions will be established to<br>accommodate all areas of the development and creation of clinics for medical professionals from building construction to equipment<br>financing and administrations.</p>
  <p>The company's operation will be managed in Sherwood Park, Alberta facilitating transactions across western Canada. It will be structured<br>in a tax efficient manner for our investors. &nbsp;The income will be treated as active income to allow for an efficient growth of earnings.</p>
</div>
<div class="btn" style="left:545px;top:1137px;width:141px;height:36px">READ MORE &#8594;</div>

<!-- solutions -->
<div class="sec-title" style="top:1312px">VEL-CORA <span class="accent">SOLUTIONS</span></div>
<div class="abs band" role="img" aria-label="Blue tinted photo of business people in an office"></div>
<div class="abs sol-img" style="left:146px;background:linear-gradient(135deg,#dfe6ee,#3e7fc8 55%,#1d4f8f)" role="img" aria-label="Hand touching a hexagon interface labelled leasing"></div>
<div class="abs sol-img" style="left:626px;background:radial-gradient(circle at 50% 45%,#6aa6dc,#1b4f8e 55%,#0b2d5a)" role="img" aria-label="Open hand holding a glowing security shield"></div>
<div class="abs sol-card" style="left:141px">
  <h3>LEASING OPERATIONS</h3>
  <p>Vel-Cora Solutions leasing division will secure an investment portfolio comprised of equipment leases and other small business financing solutions across Western Canada...[+]</p>
</div>
<div class="abs sol-card" style="left:621px">
  <h3>SECURITY MEASURES</h3>
  <p>Vel-Cora Solution leasing divison will implement a number of security measures which ensures investors are secure and returns are maximised over the elife of the investments....[+]</p>
</div>
<div class="btn" style="left:513px;top:1863px;width:172px;height:38px">CALL US TODAY &#8594;</div>

<!-- projects -->
<div class="sec-title" style="top:2037px">UPCOMING <span class="accent">PROJECTS</span></div>
<div class="abs proj-img" style="left:141px;background:linear-gradient(180deg,#9fb7d6,#dfe7f2 60%,#f3f6fa)" role="img" aria-label="Large bright empty warehouse interior"></div>
<div class="abs proj-img" style="left:454px;background:linear-gradient(180deg,#0c3d8f 0%,#2b63b3 30%,#a58b78 45%,#6b5c52 100%)" role="img" aria-label="Historic brick office building under a blue sky"></div>
<div class="abs proj-img" style="left:767px;background:linear-gradient(180deg,#e8e6e0,#b8b3aa 55%,#6d6a63)" role="img" aria-label="Modern office lobby with plants and glass block wall"></div>
<div class="abs proj-card" style="left:163px"><h4>Pinegrove Business Park</h4><p>The Pinegrove Business Park in Langford, British Columbia on Vaancouver...{+}</p></div>
<div class="abs proj-card" style="left:476px"><h4>Holtmere Business Park</h4><p>The city of Holtmere is a core municipalty in the Western Communities...{+}</p></div>
<div class="abs proj-card" style="left:789px"><h4 class="long">Mt. Corwin Ridge Professional</h4><p>Mt. Corwin Professional building will feature a repurposed building adjacent....{+}</p></div>
<div class="abs arrow" style="left:86px;background:var(--white);border:1px solid #ccc"><svg width="10" height="10" viewBox="0 0 10 10"><path d="M6.5 1.5L3 5l3.5 3.5" fill="none" stroke="#333" stroke-width="1.5"/></svg></div>
<div class="abs arrow" style="left:1080px;background:var(--green)"><svg width="10" height="10" viewBox="0 0 10 10"><path d="M3.5 1.5L7 5 3.5 8.5" fill="none" stroke="#fff" stroke-width="1.5"/></svg></div>

<!-- team -->
<div class="abs team-bg"></div>
<div class="abs tab tab-outline" style="left:386px;width:173px">OUR PARTNERS</div>
<div class="abs tab tab-filled" style="left:579px;width:234px">OUR MANAGEMENT TEAM</div>

<div class="abs member" style="left:141px">
  <div class="abs member-photo" style="background:linear-gradient(180deg,#c9cdd2,#e6e8ea 60%,#9aa4ae)" role="img" aria-label="Portrait of Gil Parish in a white coat"></div>
  <div class="abs member-info">
    <h5>Gil Parish</h5>
    <div class="member-brand">firmstance</div>
    <p>Lorem ipsum dolor sit amet, uirhtgijj consectetuer adipiscing elit, sedgtdl diam nonummy nibh euismod afweq tincidunt ut laoreet dolore magnafrt aliquam erat volutpat.</p>
  </div>
</div>
<div class="abs member" style="left:621px">
  <div class="abs member-photo" style="background:linear-gradient(180deg,#7fb2d8,#4a88b5 55%,#2a4f6b)" role="img" aria-label="Portrait of Dietmar Vellasquin outdoors by the sea"></div>
  <div class="abs member-info">
    <h5>Dietmar Vellasquin</h5>
    <div class="member-brand">GSH Dental</div>
    <p>Lorem ipsum dolor sit amet, uirhtgijj consectetuer adipiscing elit, sedgtdl diam nonummy nibh euismod afweq tincidunt ut laoreet dolore magnafrt aliquam erat volutpat.</p>
  </div>
</div>

<!-- footer -->
<div class="abs footer"></div>
<div class="abs fnav" style="left:329px">HOME</div>
<div class="abs fsep" style="left:411px"></div>
<div class="abs fnav" style="left:453px">ABOUT US</div>
<div class="abs fsep" style="left:565px"></div>
<div class="abs fnav" style="left:606px">WHAT WE DO</div>
<div class="abs fsep" style="left:739px"></div>
<div class="abs fnav" style="left:782px">CONTACT US</div>
<div class="abs fline"></div>

<div class="abs fcontact" style="left:142px">
  <div class="ficon"><svg width="16" height="16" viewBox="0 0 24 24" fill="#fff"><path d="M5 3h4l2 5-3 2a12 12 0 0 0 6 6l2-3 5 2v4a2 2 0 0 1-2 2A17 17 0 0 1 3 5a2 2 0 0 1 2-2z"/></svg></div>
  <div><h6>Call Us</h6><p>+1 123 456 7890</p></div>
</div>
<div class="abs fdiv" style="left:365px"></div>
<div class="abs fcontact" style="left:453px">
  <div class="ficon"><svg width="15" height="12" viewBox="0 0 24 18" fill="#fff"><path d="M1 1h22v16H1z"/><path d="M1 2l11 8 11-8" fill="none" stroke="#8cc63f" stroke-width="2"/></svg></div>
  <div><h6>Email</h6><p>info@velcorahealth.com</p></div>
</div>
<div class="abs fdiv" style="left:737px"></div>
<div class="abs fcontact" style="left:826px">
  <div class="ficon"><svg width="12" height="16" viewBox="0 0 12 16" fill="#fff"><path d="M6 0a6 6 0 0 0-6 6c0 4.5 6 10 6 10s6-5.5 6-10a6 6 0 0 0-6-6zm0 8.5A2.5 2.5 0 1 1 6 3.5a2.5 2.5 0 0 1 0 5z"/></svg></div>
  <div><h6>Address</h6><p>123, Lorem Ipsum dolor sit ame<br>Lorem Ipsum is simply dumm</p></div>
</div>

<div class="abs copy">Copyright © 2020 VEL-CORA SOLUTIONS. All Rights Reserved.</div>
<div class="abs social" style="left:969px"></div>
<div class="abs social" style="left:1001px"></div>
<div class="abs social" style="left:1034px"></div>

</body>
</html>
```